Velmoria-Quillmesh Partial Redesign - Web App

Are you able to apply your creativity to an existing layout? I’m convinced that even just a few touches can make a big difference to add personality and professionalism to a website design, and I’m looking for someone able to use existing ideas and bring them to the next level while keeping inside some given constraints.
The actual job is to improve an existing design concept and to apply it creatively to a landing page, a simple home page, and an older web app (single page website).
To help you start with a clear picture of the current situation and of my requirements, I created a detailed brief with screenshots, live examples, and complete instructions. You can find it attached to this job.
My tastes are inclined towards clean and simple designs. For this project I'm not looking for dazzling novelty, but for very solid craftsmanship. Are the right man - or woman - for the job?
Updates
I wanted to thank everybody who participated in this project. I made a choice, but also other designs were interesting. Hope to work with you another time.
Target Market(s)
Our main target is social media marketers and startuppers
Look and feel
Each slider illustrates characteristics of the customer's brand and the style your logo design should communicate.

```html
<!DOCTYPE html>
<html lang="en">
<head>
<meta charset="utf-8">
<title>Velmoria – Tour Influencers Analysis</title>
<link rel="stylesheet" href="https://fonts.googleapis.com/css2?family=Arimo:wght@400;700&display=swap">
<style>
  :root {
    --page-bg: #ffffff;
    --panel-bg: #f3f3f3;
    --panel-border: #c9c9c9;
    --header-bg: #9fa8ac;
    --header-text: #ffffff;
    --ink: #111111;
    --blue: #2c86cc;
    --red: #dc3912;
    --footer-top: #2e2e2e;
    --footer-bottom: #262626;
    --footer-text: #ffffff;
    --footer-rule: #4a4a4a;
  }
  * { box-sizing: border-box; margin: 0; padding: 0; }
  html, body {
    width: 1200px; height: 668px; overflow: hidden;
    background: var(--page-bg);
    font-family: "Arimo", Arial, sans-serif;
    color: var(--ink);
  }
  .canvas { position: relative; width: 1200px; height: 668px; }

  .analysis-panel {
    position: absolute; left: 35px; top: -10px; width: 1130px; height: 511px;
    background: var(--panel-bg);
    border: 1px solid var(--panel-border);
    border-top: none;
    border-radius: 0 0 5px 5px;
    box-shadow: 0 1px 2px rgba(0,0,0,.18);
  }
  .section-header {
    position: absolute; left: 47px; top: 21px; width: 1106px; height: 38px;
    background: var(--header-bg); border-radius: 5px;
    color: var(--header-text); font-size: 24px; letter-spacing: .5px;
    text-align: center; line-height: 38px;
  }

  .chart { position: absolute; top: 0; width: 500px; height: 500px; }
  .chart-title {
    position: absolute; top: 128px; width: 100%;
    font-size: 19px; font-weight: 700; text-align: center;
  }
  .chart-pie { position: absolute; left: 0; top: 0; }
  .chart-legend {
    position: absolute; top: 197px; list-style: none; font-size: 14.5px; line-height: 17px;
  }
  .chart-legend li { position: relative; padding-left: 19px; margin-bottom: 6px; }
  .chart-legend li::before {
    content: ""; position: absolute; left: 0; top: 2px; width: 12px; height: 12px;
  }
  .chart-legend .is-blue::before { background: var(--blue); }
  .chart-legend .is-red::before { background: var(--red); }

  .chart--internet { left: 62px; }
  .chart--internet .chart-legend { left: 367px; }
  .chart--influencers { left: 615px; }
  .chart--influencers .chart-legend { left: 367px; }

  .site-footer {
    position: absolute; left: 0; top: 528px; width: 1200px; height: 140px;
    background: linear-gradient(var(--footer-top), var(--footer-bottom));
    color: var(--footer-text); font-size: 14.5px;
  }
  .footer-brand {
    position: absolute; left: 47px; top: 22px; display: flex; align-items: center; gap: 10px;
    font-size: 20px; font-weight: 700;
  }
  .footer-brand-mark { width: 14px; height: 14px; border-radius: 50%; background: var(--footer-text); }
  .footer-rule { position: absolute; left: 47px; top: 66px; width: 168px; border-top: 1px solid var(--footer-rule); }
  .footer-address { position: absolute; left: 47px; top: 80px; font-style: normal; line-height: 24px; }
  .footer-copyright { position: absolute; left: 0; width: 1204px; top: 92px; text-align: center; }
  .footer-links { position: absolute; right: 47px; top: 92px; display: flex; gap: 17px; list-style: none; }
  .footer-links a { color: var(--footer-text); text-decoration: none; }
</style>
</head>
<body>
<div class="canvas">
  <section class="analysis-panel" aria-labelledby="analysis-title"></section>
  <h1 class="section-header" id="analysis-title">TOUR INFLUENCERS ANALYSIS</h1>

  <figure class="chart chart--internet">
    <figcaption class="chart-title">Your Influencers vs Rest Of The Internet</figcaption>
    <svg class="chart-pie" width="500" height="500" viewBox="0 0 500 500" aria-label="Tracked influencers 75%, others 25%">
      <path d="M234 333 L342 333 A108 108 0 1 1 234 225 Z" fill="var(--blue)" stroke="#fff" stroke-width="1"/>
      <path d="M234 333 L234 225 A108 108 0 0 1 342 333 Z" fill="var(--red)" stroke="#fff" stroke-width="1"/>
      <text x="284" y="299" fill="#fff" font-size="14" text-anchor="middle" font-family="Arimo, Arial, sans-serif">25%</text>
      <text x="202" y="374" fill="#fff" font-size="14" text-anchor="middle" font-family="Arimo, Arial, sans-serif">75%</text>
    </svg>
    <ul class="chart-legend">
      <li class="is-blue">Tracked<br>Influencers</li>
      <li class="is-red">Others</li>
    </ul>
  </figure>

  <figure class="chart chart--influencers">
    <figcaption class="chart-title">Your Influencers vs Your influencers</figcaption>
    <svg class="chart-pie" width="500" height="500" viewBox="0 0 500 500" aria-label="mossyfinch 75%, joelwren 25%">
      <path d="M234 333 L342 333 A108 108 0 1 1 234 225 Z" fill="var(--blue)" stroke="#fff" stroke-width="1"/>
      <path d="M234 333 L234 225 A108 108 0 0 1 342 333 Z" fill="var(--red)" stroke="#fff" stroke-width="1"/>
      <text x="284" y="299" fill="#fff" font-size="14" text-anchor="middle" font-family="Arimo, Arial, sans-serif">25%</text>
      <text x="202" y="374" fill="#fff" font-size="14" text-anchor="middle" font-family="Arimo, Arial, sans-serif">75%</text>
    </svg>
    <ul class="chart-legend">
      <li class="is-blue">mossyfinch...</li>
      <li class="is-red">joelwren</li>
    </ul>
  </figure>

  <footer class="site-footer">
    <div class="footer-brand"><span class="footer-brand-mark"></span>Velmoria</div>
    <div class="footer-rule"></div>
    <address class="footer-address">48 Larkfield Lane<br>N7 4QT Ashbury, UK</address>
    <p class="footer-copyright">Copyright © 2012 Velmoria Ltd.</p>
    <ul class="footer-links">
      <li><a href="#">Private Policy</a></li>
      <li><a href="#">Term Of Services</a></li>
    </ul>
  </footer>
</div>
</body>
</html>
```